VELKO Website Redesign in Wix

Task:
Create a new design for all pages of the VELKO technology website in Wix. Specifications are:
Color palette preferences: black, white, gray, purple, blue. See VELKO Ref Doc provided.
Please refer to the VELKO_ref doc for a sample of the desired color palette
Typesetting must be in Montserrat
Brand will be that of a Marketing Technology company
Looking for vibrant, highly engaging images and organized, digestible flow. Open to suggestions
Required format is Wix.
VELKO logo does NOT need to be redesigned. Please use the files provided for the VELKO logo.
Look and feel
Each slider illustrates characteristics of the customer's brand and the style your logo design should communicate.

```html
<!DOCTYPE html>
<html lang="en">
<head>
<meta charset="utf-8">
<title>VELKO — Marketing Technology</title>
<link href="https://fonts.googleapis.com/css2?family=Montserrat:wght@400;500;600;700;800&family=Roboto:wght@400;500&display=swap" rel="stylesheet">
<style>
:root{
  --ink:#111111;
  --white:#ffffff;
  --blue:#1c7ac7;
  --blue-deep:#0f5fa6;
  --hero-dark:#0a1a2c;
  --hero-mid:#0f3550;
  --grey-bg:#f3f4f6;
  --cell:#e8e9ec;
  --tick:#3cb043;
  --cross:#e0211c;
  --footer:#111111;
}
*{box-sizing:border-box;margin:0;padding:0}
html,body{width:1200px;height:3841px;overflow:hidden}
body{font-family:"Roboto",sans-serif;color:var(--ink);background:var(--white)}
.site-header{height:77px;display:flex;align-items:center;padding:0 112px;justify-content:space-between;background:var(--white)}
.brand{font-family:"Montserrat",sans-serif;font-weight:700;font-size:50px;letter-spacing:10px;color:var(--ink)}
.main-nav{display:flex;gap:30px;font-size:16px;font-weight:500;letter-spacing:.3px}
.hero{height:629px;position:relative;background:radial-gradient(circle at 55% 55%,#3a2a30 0,#10304a 25%,var(--hero-mid) 45%,var(--hero-dark) 100%);color:var(--white);padding:235px 0 0 112px}
.hero-art{position:absolute;inset:0}
.hero-content{position:relative}
.hero-title{font-family:"Montserrat",sans-serif;font-weight:700;font-size:118px;letter-spacing:22px;line-height:1}
.hero-text{margin-top:14px;width:470px;font-size:19px;line-height:31px}
.btn{display:inline-block;border:2px solid currentColor;border-radius:24px;padding:11px 26px;font-size:16px;font-weight:500}
.hero .btn{margin-top:26px}
.about{height:589px;display:flex}
.about-copy{width:600px;padding:98px 0 0 112px}
.rule{width:45px;height:2px;background:currentColor;margin-bottom:12px}
.section-h{font-family:"Montserrat",sans-serif;font-weight:700;font-size:38px}
.about-text{margin-top:28px;width:440px;font-size:14.5px;line-height:30px}
.about .btn{margin-top:30px;padding:12px 30px}
.about-photo{flex:1;background:linear-gradient(135deg,#5d6a55 0,#8e8f8a 35%,#1c1c1e 55%,#b8b6b2 100%)}
.platform{height:846px;background:radial-gradient(circle at 50% 40%,#2a8ad4,var(--blue) 45%,var(--blue-deep));color:var(--white);text-align:center;padding-top:80px;position:relative}
.platform-text{width:940px;margin:16px auto 0;font-size:14.5px;line-height:30px}
.platform .section-h{font-size:35px}
.strategy-h{margin-top:48px}
.strategy-art{position:absolute;left:230px;top:330px;width:740px;height:440px;border-radius:24px;background:radial-gradient(circle at 53% 49%,#ffffff 0,#ffffff 96px,rgba(255,255,255,.12) 150px,rgba(255,255,255,.05) 100%)}
.strategy-labels{position:absolute;left:0;top:0;pointer-events:none}
.awards{height:471px;text-align:center;padding-top:72px}
.awards .section-h{font-size:36px}
.award-row{display:flex;gap:54px;justify-content:center;margin-top:48px}
.award-card{width:202px;height:206px;box-shadow:0 1px 5px rgba(0,0,0,.22);padding:16px 10px;font-size:18px;line-height:23px;color:#222}
.award-badge{width:70px;height:70px;border-radius:50%;background:#d9d9d9;margin:0 auto 16px}
.award-card.small{font-size:10px;line-height:12px}
.award-card .award-name{display:block;font-size:17px;line-height:24px;white-space:nowrap;margin-bottom:6px}
.compare{height:553px;background:var(--grey-bg);text-align:center;padding-top:84px}
.compare .section-h{font-size:35px}
.compare-table{margin:30px auto 0;border-spacing:4px;font-family:"Montserrat",sans-serif}
.compare-table th{background:var(--blue);color:var(--white);font-weight:500;font-size:19px;height:67px;width:125px;vertical-align:bottom;padding-bottom:4px}
.compare-table th.feat{width:166px;vertical-align:middle}
.compare-table td{background:var(--cell);height:39px}
.compare-table td.label{padding:0 22px;font-size:11px;line-height:12px}
.compare-table td.mark{font-size:26px;font-weight:800;line-height:1}
.compare-table td.yes{color:var(--tick)}
.compare-table td.no{color:var(--cross)}
.site-footer{height:675px;background:var(--footer);color:var(--white);display:flex;padding:100px 112px 0}
.contact{width:543px}
.contact .section-h{font-size:22px}
.contact p{font-size:19px;margin-top:20px;color:var(--white)}
.contact .addr{margin-top:14px}
.contact .gap{margin-top:46px}
.social{display:flex;gap:16px;margin-top:80px}
.social span{width:20px;height:20px;border-radius:50%;background:var(--white)}
.contact .copyright{font-size:14px;margin-top:78px}
.form{width:435px;padding-top:6px}
.form label{display:block;font-size:14px;margin-bottom:12px}
.field{height:52px;border:1px solid var(--white);margin-bottom:22px}
.field.tall{height:108px}
.submit{float:right;width:163px;height:46px;border:2px solid var(--white);border-radius:24px;text-align:center;line-height:42px;font-size:16px;font-weight:500;margin-top:18px}
</style>
</head>
<body>
<header class="site-header">
  <div class="brand">VELKO</div>
  <nav class="main-nav"><span>HOME</span><span>HOW IT WORKS</span><span>VELKO APPLICATIONS</span><span>COMPANY</span><span>CONTACT US</span><span>MORE</span></nav>
</header>

<section class="hero">
  <div class="hero-art" role="img" aria-label="Glowing network of connected nodes around a cloud symbol on a dark blue background"></div>
  <div class="hero-content">
    <h1 class="hero-title">VELKO</h1>
    <p class="hero-text">Increase and perfect your connection with consumers using VELKO™'s patented self-service content delivery technology</p>
    <span class="btn">GET STARTED</span>
  </div>
</section>

<section class="about">
  <div class="about-copy">
    <div class="rule"></div>
    <h2 class="section-h">ABOUT US</h2>
    <p class="about-text">VELKO™ Technology is a revolutionary platform that uses high frequency tones (known as VELKO packets) imperceptible to the human ear. VELKO's patented technology embeds information on an audio file for a more targeted, enhanced user experience via music, video, text, virtual reality, augmented reality, and other content. It is a modern-day solution to an age-old problem--establishing two-way communication with a consumer rather than listening to what they have to say.</p>
    <span class="btn">LEARN MORE</span>
  </div>
  <div class="about-photo" role="img" aria-label="Hands holding a tablet showing a SaaS cloud diagram on a desk"></div>
</section>

<section class="platform">
  <h2 class="section-h">OUR REVOLUTIONARY PLATFORM</h2>
  <p class="platform-text">Whether you're marketing software, selling a product, or looking to close a deal – find out your target market and quickly modify your campaigns to reach consumers silently and securely. Our platform goes far beyond basic ad optimization to deliver individualized content that immediately increases engagement over any communication medium with embedded tones.</p>
  <h2 class="section-h strategy-h">STRATEGY TOWARDS MARKET DOMINANCE</h2>
  <div class="strategy-art" role="img" aria-label="Segmented ring diagram with the SaaS platform at its centre and eight revenue streams branching out"></div>
  <svg class="strategy-labels" width="1200" height="846" viewBox="0 0 1200 846" font-family="Montserrat, sans-serif" font-size="15" fill="#fff">
    <text x="623" y="350" text-anchor="middle">Corporate Subscriptions</text>
    <text x="240" y="394">Data and Analytics Models Our</text>
    <text x="240" y="410">Value is Unlocked Inside Scale</text>
    <text x="748" y="394">AD Tech Licensing</text>
    <text x="259" y="523">Digital Rights</text>
    <text x="259" y="539">Management Applications</text>
    <text x="774" y="524">Platform Integrations</text>
    <text x="296" y="652">NFT Security</text>
    <text x="774" y="657">Technology Licensing</text>
    <text x="638" y="754" text-anchor="middle">Advertising Campaigns</text>
    <g fill="#111" font-weight="700" font-size="24" text-anchor="middle">
      <text x="624" y="545">Software as</text><text x="624" y="572">a Service</text>
      <text x="624" y="599">(SaaS)</text><text x="624" y="626">Platform</text>
    </g>
  </svg>
</section>

<section class="awards">
  <h2 class="section-h">AWARDS</h2>
  <div class="award-row">
    <div class="award-card"><div class="award-badge"></div>Northlight Founder of The Year® 1995 Mountain Desert Award Finalist</div>
    <div class="award-card small"><div class="award-badge"></div><span class="award-name">BRIGHTBULB AWARDS</span>Brightbulb Award - Gold Winner for innovation in the category of "Lifestyle and Social Impact; Quality of Life" in 2013 for SoundSight®</div>
    <div class="award-card"><div class="award-badge"></div>Market Ledger<br>30 under 30</div>
    <div class="award-card"><div class="award-badge"></div>Market Ledger<br>40 under 40</div>
  </div>
</section>

<section class="compare">
  <h2 class="section-h">CURRENT TECHNOLOGY VS VELKO™</h2>
  <table class="compare-table">
    <thead><tr><th class="feat">Features</th><th>VELKO</th><th>WLAN</th><th>Pairing</th><th>RFID</th><th>NFC</th><th>Social</th></tr></thead>
    <tbody>
      <tr><td class="label">operates without a network</td><td class="mark yes">✓</td><td class="mark no">✕</td><td class="mark no">✕</td><td class="mark no">✕</td><td class="mark no">✕</td><td class="mark no">✕</td></tr>
      <tr><td class="label">operates without live power</td><td class="mark yes">✓</td><td class="mark no">✕</td><td class="mark no">✕</td><td class="mark no">✕</td><td class="mark no">✕</td><td class="mark no">✕</td></tr>
      <tr><td class="label">transmits data securely</td><td class="mark yes">✓</td><td class="mark yes">✓</td><td class="mark yes">✓</td><td class="mark yes">✓</td><td class="mark yes">✓</td><td class="mark no">✕</td></tr>
      <tr><td class="label">private</td><td class="mark yes">✓</td><td class="mark yes">✓</td><td class="mark yes">✓</td><td class="mark yes">✓</td><td class="mark yes">✓</td><td class="mark no">✕</td></tr>
      <tr><td class="label">customization</td><td class="mark yes">✓</td><td class="mark yes">✓</td><td class="mark yes">✓</td><td class="mark yes">✓</td><td class="mark yes">✓</td><td class="mark yes">✓</td></tr>
      <tr><td class="label">carried by audio soundwaves</td><td class="mark yes">✓</td><td class="mark no">✕</td><td class="mark no">✕</td><td class="mark no">✕</td><td class="mark no">✕</td><td class="mark no">✕</td></tr>
    </tbody>
  </table>
</section>

<footer class="site-footer">
  <div class="contact">
    <div class="rule"></div>
    <h2 class="section-h">CONTACT</h2>
    <p class="addr">412 Harlow Ave, Brookfield, NY 10990, USA</p>
    <p class="gap">Phone 1-800-555-0147</p>
    <p>Email hello@velkotech.example</p>
    <div class="social"><span></span><span></span><span></span><span></span></div>
    <p class="copyright">©Copyright ©2022 VELKO™. All Rights Reserved.</p>
  </div>
  <form class="form">
    <label>Enter Your Name</label><div class="field"></div>
    <label>Enter Your Email*</label><div class="field"></div>
    <label>Enter Your Subject</label><div class="field"></div>
    <label>Message</label><div class="field tall"></div>
    <div class="submit">SUBMIT</div>
  </form>
</footer>
</body>
</html>
```